Design my site www.brieflyledger.com

So here is what I am thinking in terms of design:

https://plenvo.com

https://www.skyluxair.com

http://kalvex.com/harbor-plaza-tower/

I want the theme to be white and blue (royal blue). I attached a paint picture of what I would like the site to look like in terms of placing the text. Generally, what I like about the sites above is that they are simple, you can navigate easily and have some kind of idea of what's going on by looking at the center (picture and motto). Let's establish a clear understanding of how the functional part of the site would look like. Please see the picture attached.

I want to keep it simple: On top would be the Name 'BRIEFLY ledger", somewhere to the right on top on the page would be 'Sign in" button.

In the center would be a picture (maybe a video) with the Motto (on top of it all in capital) OBSERVE NAVIGATE DECIDE and below would be the "sign up now"

Below the picture (like on kalvex.com site) or to the left on top of the page would be "About Us', "Press" "Contact Us' buttons.

Then once the user gets to his page his got 3 tabs " Press Headlines", "Events", " Briefings".

we would keep the same format I only have on the site, but separate for every Tab.

I do not want the user to get distracted. I also want him to be able to access the page though mobile phone and be able to get automatic updates just like Zorvan Pings without having to sign in daily.

The landing page must be minimalist yet with business/corporate feel where users can navigate easily and a "what you see is what you get" approach. You want an image or video (personally I prefer the video.. it does capture the users attention instantly, as long as it is an interesting video), with your taglines in it.

Sections available to public: About Us, Contact Us, Landing Page with Signup Option

Private: Public Sections + User Account Page, Tabs for (Events, Press Headlines, Briefings)

Target Market(s)

PR/media monitoring/diplomatic community

Coding

Coded - Design and coding required

Number of Pages Required

1 page

Font styles to use
Serif
Sans Serif

Colors
0255a3
ec1f27

Requirements
Must have
• a simple landing page, that is user friendly.
Nice to have
• a video with the explanation of how to navigate the site
Should not have
• too many colors, graphs etc.

```html
<!DOCTYPE html>
<html lang="en">
<head>
<meta charset="utf-8">
<title>BRIEFLY ledger — Press Headlines</title>
<link rel="stylesheet" href="https://fonts.googleapis.com/css2?family=Open+Sans:wght@400;600;700&display=swap">
<style>
  :root {
    --royal: #023a7b;
    --royal-deep: #1d3f72;
    --royal-mid: #2f5590;
    --ink: #111111;
    --rule-dark: #3a3a3a;
    --panel: #cfcfcf;
    --panel-edge: #c2c2c2;
    --white: #ffffff;
  }
  * { box-sizing: border-box; margin: 0; padding: 0; }
  html, body {
    width: 1200px;
    height: 640px;
    overflow: hidden;
    background: var(--white);
    font-family: "Open Sans", Arial, sans-serif;
    color: var(--ink);
  }
  .page { position: relative; width: 1200px; height: 640px; }

  .site-header {
    position: absolute; left: 0; top: 0;
    width: 1200px; height: 84px;
    background: linear-gradient(90deg, var(--royal-mid) 0%, var(--royal-deep) 45%, var(--royal-mid) 100%);
  }
  .site-header .skyline {
    position: absolute; inset: 0;
    background: linear-gradient(180deg, rgba(255,255,255,0.06) 0%, rgba(0,0,0,0.08) 100%);
  }
  .brand {
    position: absolute; left: 132px; top: 27px;
    font-weight: 700; font-size: 24px; line-height: 30px;
    color: var(--white); letter-spacing: 0.5px;
  }
  .btn-signup {
    position: absolute; left: 979px; top: 26px;
    width: 88px; height: 31px;
    border: 1px solid var(--white); border-radius: 16px;
    color: var(--white); font-weight: 700; font-size: 11px;
    display: flex; align-items: center; justify-content: center;
    text-decoration: none; letter-spacing: 0.3px;
  }

  .tab-nav {
    position: absolute; left: 133px; top: 144px;
    width: 204px; height: 318px;
    background: var(--panel);
    border: 1px solid var(--panel-edge);
    border-top: none;
  }
  .tab-nav ul { list-style: none; }
  .tab {
    height: 46px; display: flex; align-items: center;
    padding-left: 21px; font-size: 13px;
    color: var(--royal);
    border-bottom: 1px solid var(--white);
  }
  .tab.is-active {
    position: relative; margin: 0 -1px;
    width: 221px; height: 47px;
    padding-left: 22px;
    background: var(--royal); color: var(--white);
    clip-path: polygon(0 0, 204px 0, 100% 50%, 204px 100%, 0 100%);
    border-bottom: none;
    margin-bottom: 1px;
  }

  .feed { position: absolute; left: 426px; top: 144px; width: 642px; }
  .story { height: 238px; }
  .story-title {
    font-weight: 400; font-size: 24px; line-height: 30px;
    color: var(--royal); white-space: pre;
  }
  .story-rule { height: 1px; margin: 8px 0 10px 2px; background: var(--rule-dark); }
  .story:nth-child(2) .story-rule { background: var(--royal); }
  .story-body {
    margin-left: 2px; font-size: 13px; line-height: 19.3px; color: var(--ink);
  }
  .story-meta {
    margin: 20px 0 0 2px; display: flex; align-items: center;
    font-size: 13px; line-height: 19px;
  }
  .story-meta .sep {
    width: 1px; height: 20px; background: var(--ink); margin: 0 12px;
  }
</style>
</head>
<body>
<div class="page">
  <header class="site-header">
    <div class="skyline" role="img" aria-label="City skyline photograph tinted royal blue"></div>
    <div class="brand">BRIEFLY ledger</div>
    <a class="btn-signup" href="#">SIGN UP</a>
  </header>

  <nav class="tab-nav" aria-label="Account tabs">
    <ul>
      <li class="tab is-active">Newspapers Headlines</li>
      <li class="tab">Events</li>
      <li class="tab">Daily Briefing</li>
    </ul>
  </nav>

  <main class="feed">
    <article class="story">
      <h2 class="story-title">Nulla  facilisis at vero eros et accumsan</h2>
      <div class="story-rule"></div>
      <p class="story-body">Duis autem vel eum iriure dolor in hendrerit vulputate velit esse molestievel illum dolore eu feugiat facilisis at vero eros et accumsan et iusto odio duis autem vel eum iriure dolor duis autem vel eum iriure dolor in hendrerit vulputate velit esse molestievel illum dolore eu feugiat facilisis at vero eros et accumsan et iusto odio Duis autem vel eum iriure dolor duis autem</p>
      <div class="story-meta"><span>Jan 05, 2016</span><span class="sep"></span><span>Source</span></div>
    </article>
    <article class="story">
      <h2 class="story-title">Nulla  facilisis at vero eros et accumsan</h2>
      <div class="story-rule"></div>
      <p class="story-body">Duis autem vel eum iriure dolor in hendrerit vulputate velit esse molestievel illum dolore eu feugiat facilisis at vero eros et accumsan et iusto odio duis autem vel eum iriure dolor duis autem vel eum iriure dolor in hendrerit vulputate velit esse molestievel illum dolore eu feugiat facilisis at vero eros et accumsan et iusto odio Duis autem vel eum iriure dolor duis autem</p>
      <div class="story-meta"><span>Jan 05, 2016</span><span class="sep"></span><span>Source</span></div>
    </article>
  </main>
</div>
</body>
</html>
```